Letterhead for a German Distribution/Manufacturing Company

We need a professional Letterhead in a unique Design.
not to playful.
The Letterhead has to show show that we are a international company with headquater in Westmark.
all details like adress, Vat Tax Number, Bank Accout, Eori, email, Company number has to be on the Letterhead.
for example use: VAT TAX DE5470318 Bank Account: Kestrel Bank IBAN DE412058731ß204683 Swift: MORV0417352 EORI 3150428697 Company Number: HRB 51806 Adress: VOLMINTA UG Ahornweg 7 Postal Code 06384 City Lindmar Country: Westmark Email: info@volminta-example.com
the design can be colored but doesnt have to be
Industry/Entity Type
Manufacturing and international distribution
Requirements
Must have
- show that we are a international company with headquater in Westmark. our company infos and logo

```html
<!DOCTYPE html>
<html lang="de">
<head>
<meta charset="utf-8">
<title>VOLMINTA UG – Briefbogen</title>
<link rel="stylesheet" href="https://fonts.googleapis.com/css2?family=Nunito+Sans:wght@400;600&family=Arimo:wght@400&display=swap">
<style>
  :root {
    --paper: #ffffff;
    --paper-shade: #f2f2f3;
    --ink-dark: #2b2a2c;
    --ink-mid: #5a5a5c;
    --ink-soft: #6a6a6c;
  }
  * { margin: 0; padding: 0; box-sizing: border-box; }
  html, body {
    width: 1084px;
    height: 1200px;
    overflow: hidden;
    background: var(--paper);
  }
  .letterhead {
    position: relative;
    width: 1084px;
    height: 1200px;
    background: linear-gradient(180deg, var(--paper) 0%, var(--paper) 12%, var(--paper-shade) 100%);
    font-family: "Arimo", Arial, sans-serif;
    color: var(--ink-mid);
  }
  .brand {
    position: absolute;
    left: 106px;
    top: 80px;
    display: flex;
    align-items: center;
    gap: 22px;
  }
  .brand-dot {
    width: 86px;
    height: 86px;
    border-radius: 50%;
    background: var(--ink-dark);
  }
  .brand-name {
    font-family: "Nunito Sans", Arial, sans-serif;
    font-weight: 400;
    font-size: 58px;
    letter-spacing: 0.5px;
    color: var(--ink-dark);
  }
  .sender {
    position: absolute;
    left: 765px;
    top: 66px;
    font-size: 15.5px;
    line-height: 18px;
  }
  .sender-address { font-style: normal; margin-bottom: 6px; }
  .contact-list { list-style: none; }
  .contact-list li {
    display: flex;
    align-items: center;
    gap: 8px;
    line-height: 19px;
  }
  .contact-list svg { width: 15px; height: 15px; flex: none; fill: var(--ink-dark); }
  .legal-footer {
    position: absolute;
    left: 0;
    right: 0;
    top: 1124px;
    text-align: center;
    font-size: 15.5px;
    line-height: 22px;
    color: var(--ink-soft);
  }
</style>
</head>
<body>
<main class="letterhead">
  <header>
    <div class="brand">
      <span class="brand-dot"></span>
      <span class="brand-name">VOLMINTA</span>
    </div>
    <div class="sender">
      <address class="sender-address">
        VOLMINTA UG<br>
        Ahornweg 7 06384<br>
        City Lindmar Westmark
      </address>
      <ul class="contact-list">
        <li>
          <svg viewBox="0 0 16 16" aria-hidden="true"><path d="M1 5c0-2 3-3 7-3s7 1 7 3v1h-3V5H4v1H1z M4 7h8l2 7H2z M8 9a2 2 0 1 0 0 .01z"/></svg>
          555.014.2736
        </li>
        <li>
          <svg viewBox="0 0 16 16" aria-hidden="true"><path d="M1 4h14v1L8 9 1 5z M1 6.5l7 4 7-4V12H1z"/></svg>
          info@volminta-example.com
        </li>
        <li>
          <svg viewBox="0 0 16 16" aria-hidden="true"><path d="M8 1a7 7 0 1 0 0 14A7 7 0 0 0 8 1zm-1 3c1 0 2 1 1 2s-2 0-2 2 2 1 2 3-2 2-3 1-1-3-2-4 1-4 4-4zm4 1c1 1 2 3 1 5-1 1-2 0-2-1s1-1 1-2-1-1 0-2z"/></svg>
          www.volminta-example.com
        </li>
      </ul>
    </div>
  </header>
  <footer class="legal-footer">
    VAT TAX DE5470318 | Bank Account: Kestrel Bank IBAN DE412058731ß204683<br>
    Swift: MORV0417352 EORI 3150428697 | Company Number: HRB 51806
  </footer>
</main>
</body>
</html>
```